Landing Page Design for Adult Dating Age Verification (18+)

The objective of this task is to design a visually appealing pre-landing page for the adult dating site "Quillmera (site: https://quillmera.com/)" with an age verification mechanism. The pre-landing page will feature two buttons that redirect visitors to the main offer. The design should also include a footer block that includes links to the terms of use, privacy policy, and contact us pages.

Design Requirements:
Develop an age verification section prominently displayed on the pre-landing page.
Design the section to include two buttons labeled "Yes" and "No" for visitors to confirm their age.
Ensure the section is visually appealing and clearly communicates the purpose of age verification.

Visual Appeal:
Create a visually appealing design that aligns with the branding and theme of the "Quillmera" adult dating site.
Use suitable color schemes, typography, and graphics to enhance the overall visual appeal of the pre-landing page.

Layout and Navigation:
Design an engaging and intuitive layout that encourages visitors to interact with the page and proceed to the main offer.
Ensure clear and visible navigation elements that direct visitors to the main offer or provide additional information.

Responsive Design:
Develop a responsive design that provides a seamless user experience across various devices, including desktop and mobile.
Ensure the design elements and layout adapt well to different screen sizes and resolutions.

File Formats and Assets:
Deliver the final design in PSD, AI, or Sketch format, ensuring that the files are well-organized and layered.
Include any necessary images or assets used in the design, ensuring they are of high quality and optimized for web use.

```html
<!DOCTYPE html>
<html lang="en">
<head>
<meta charset="UTF-8">
<title>Quillmera – Age Verification</title>
<link href="https://fonts.googleapis.com/css2?family=Roboto:wght@400;500;700&display=swap" rel="stylesheet">
<style>
  :root {
    --canvas: #ffffff;
    --ink: #0b0b0b;
    --muted: #6a6470;
    --lilac: #d2b4d6;
    --lilac-soft: #dcc3df;
    --card: #ffffff;
    --footer: #000000;
    --footer-text: #ffffff;
    --photo-warm: #d9a880;
    --photo-light: #f1e3c6;
    --photo-dark: #8e6a5c;
  }
  * { box-sizing: border-box; margin: 0; padding: 0; }
  html, body {
    width: 1123px; height: 1200px; overflow: hidden;
    background: var(--canvas);
    font-family: 'Roboto', Arial, sans-serif;
  }
  .board { position: relative; width: 1123px; height: 1200px; }
  .page {
    position: absolute; left: 63px; width: 991px; height: 496px;
    overflow: hidden;
    box-shadow: 0 2px 10px rgba(0,0,0,0.12);
  }
  .page--light { top: 81px; }
  .page--lilac { top: 618px; }
  .hero-photo {
    position: absolute; inset: 0 0 35px 0;
    background:
      radial-gradient(ellipse at 75% 55%, var(--photo-dark) 0%, rgba(142,106,92,0.6) 30%, rgba(142,106,92,0) 60%),
      linear-gradient(90deg, var(--photo-light) 0%, var(--photo-warm) 45%, #c89a7e 70%, #9c7a72 100%);
  }
  .age-gate {
    position: absolute; left: 92px; top: 54px; width: 404px; height: 360px;
    border-radius: 28px;
    text-align: center;
  }
  .page--light .age-gate { background: var(--card); }
  .page--lilac .age-gate { background: var(--lilac); }
  .brand {
    position: absolute; top: 92px; left: 0; right: 0;
    display: flex; align-items: center; justify-content: center; gap: 8px;
    font-size: 21px; font-weight: 700; color: var(--ink);
  }
  .brand-dot { width: 26px; height: 26px; border-radius: 50%; }
  .page--light .brand-dot { background: var(--lilac); }
  .page--lilac .brand-dot { background: var(--ink); }
  .age-title {
    position: absolute; top: 138px; left: 0; right: 0;
    font-size: 26px; font-weight: 500; color: var(--ink);
  }
  .age-copy {
    position: absolute; top: 184px; left: 30px; right: 30px;
    font-size: 10px; line-height: 20px; color: var(--muted);
  }
  .age-actions {
    position: absolute; top: 239px; left: 103px;
    display: flex; gap: 14px;
  }
  .btn {
    width: 92px; height: 35px; border-radius: 3px;
    display: flex; align-items: center; justify-content: center;
    font-size: 12.5px; font-weight: 500; text-decoration: none;
  }
  .page--light .btn--yes { background: var(--lilac); color: var(--ink); }
  .page--lilac .btn--yes { background: #ffffff; color: var(--ink); }
  .btn--no { background: var(--ink); color: #ffffff; }
  .site-footer {
    position: absolute; left: 0; right: 0; bottom: 0; height: 35px;
    background: var(--footer); color: var(--footer-text);
    font-size: 8.5px;
    display: flex; align-items: center;
    padding: 0 0 0 92px;
  }
  .footer-links {
    margin-left: auto; margin-right: 92px;
    display: flex; gap: 17px; align-items: center;
  }
  .footer-links a { color: var(--footer-text); text-decoration: none; }
</style>
</head>
<body>
<div class="board">

  <section class="page page--light">
    <div class="hero-photo" role="img" aria-label="Photo of a couple embracing in a warm loft bedroom"></div>
    <div class="age-gate">
      <div class="brand"><span class="brand-dot"></span>Quillmera</div>
      <h1 class="age-title">Are you over 18 years?</h1>
      <p class="age-copy">At vero eos et accusamus et iusto odio dignissimos ducimus qui<br>blanditiis praesentium voluptatum deleniti atque corrupti</p>
      <div class="age-actions">
        <a class="btn btn--yes" href="https://quillmera.com/">Yes</a>
        <a class="btn btn--no" href="#">No</a>
      </div>
    </div>
    <footer class="site-footer">
      <span>© Copyright 2023 | All Rights Reserved.</span>
      <nav class="footer-links">
        <a href="#">Terms Of Use</a><span>|</span>
        <a href="#">Privacy Policy</a><span>|</span>
        <a href="#">Contact Us</a>
      </nav>
    </footer>
  </section>

  <section class="page page--lilac">
    <div class="hero-photo" role="img" aria-label="Photo of a couple embracing in a warm loft bedroom"></div>
    <div class="age-gate">
      <div class="brand"><span class="brand-dot"></span>Quillmera</div>
      <h1 class="age-title">Are you over 18 years?</h1>
      <p class="age-copy">At vero eos et accusamus et iusto odio dignissimos ducimus qui<br>blanditiis praesentium voluptatum deleniti atque corrupti</p>
      <div class="age-actions">
        <a class="btn btn--yes" href="https://quillmera.com/">Yes</a>
        <a class="btn btn--no" href="#">No</a>
      </div>
    </div>
    <footer class="site-footer">
      <span>© Copyright 2023 | All Rights Reserved.</span>
      <nav class="footer-links">
        <a href="#">Terms Of Use</a><span>|</span>
        <a href="#">Privacy Policy</a><span>|</span>
        <a href="#">Contact Us</a>
      </nav>
    </footer>
  </section>

</div>
</body>
</html>
```